BOLD & MINIMALIST DESIGN NEEDED

We want a very bold but minimalistic business card design that is impactful and utilizes both sides of the business card. Our current logo is included for your use.

We want bold fonts and good use of negative space. We don't want the logo to overpower the design.

Target Market(s)

Professionals who are building new commercial buildings.

Industry/Entity Type

Construction

Contact Information for Business Card

Name, Title, email, office phone, cell phone, website

Font styles to use
Serif
Sans Serif

Requirements
Must have
• Bold design!

```html
<!DOCTYPE html>
<html lang="en">
<head>
<meta charset="utf-8">
<title>Ridgecrest Build – Business Card</title>
<link href="https://fonts.googleapis.com/css2?family=Montserrat:wght@400;600;800&display=swap" rel="stylesheet">
<style>
  :root {
    --green: #84c441;
    --green-light: #98cd5e;
    --green-deep: #3f7a36;
    --ink: #111111;
    --text: #333333;
    --paper: #ffffff;
    --backdrop: #ecebe8;
  }
  * { margin: 0; padding: 0; box-sizing: border-box; }
  html, body { width: 1200px; height: 1200px; overflow: hidden; }
  body {
    background: var(--backdrop);
    font-family: "Montserrat", sans-serif;
    position: relative;
  }
  .card {
    position: absolute;
    left: 220px;
    width: 760px;
    height: 434px;
    border-radius: 26px;
    overflow: hidden;
    box-shadow: 0 6px 18px rgba(0,0,0,0.18);
  }
  .card-front {
    top: 151px;
    background: linear-gradient(135deg, var(--green-light) 0%, var(--green) 45%, var(--green) 100%);
    display: flex;
    flex-direction: column;
    align-items: center;
    justify-content: center;
  }
  .front-brand {
    color: var(--green-deep);
    font-weight: 800;
    font-size: 78px;
    letter-spacing: 1px;
    line-height: 1;
    text-align: center;
  }
  .front-brand span { display: block; font-size: 34px; letter-spacing: 14px; margin-top: 14px; }
  .card-back {
    top: 614px;
    background: var(--paper);
  }
  .back-swoosh { position: absolute; inset: 0; width: 760px; height: 434px; }
  .back-brand {
    position: absolute;
    right: 30px;
    top: 140px;
    display: flex;
    align-items: center;
    gap: 14px;
  }
  .brand-square { width: 26px; height: 26px; background: var(--green); flex: none; }
  .brand-name {
    color: var(--ink);
    font-weight: 800;
    font-size: 38px;
    line-height: 1.05;
    text-align: right;
  }
  .brand-name span { display: block; font-size: 18px; letter-spacing: 9px; }
  .person { position: absolute; left: 27px; top: 188px; }
  .person-name { color: var(--green); font-weight: 600; font-size: 32px; letter-spacing: 0.5px; line-height: 1.1; }
  .person-title { color: var(--text); font-size: 18px; margin-top: 8px; letter-spacing: 0.5px; }
  .contacts {
    position: absolute; left: 27px; top: 285px;
    list-style: none; color: var(--text); font-size: 18px;
  }
  .contacts li { display: flex; align-items: center; height: 30.5px; }
  .contacts svg { width: 16px; height: 16px; margin-right: 10px; fill: var(--green); flex: none; }
  .address {
    position: absolute; right: 28px; top: 346px;
    color: var(--text); font-size: 18px; line-height: 30.5px; text-align: right;
  }
</style>
</head>
<body>
  <section class="card card-front">
    <div class="front-brand">RIDGECREST<span>BUILD</span></div>
  </section>

  <section class="card card-back">
    <svg class="back-swoosh" viewBox="0 0 760 434" aria-hidden="true">
      <path d="M0 0 H581 C330 22 100 90 0 181 Z" fill="var(--green)"/>
      <path d="M0 215 C80 110 230 52 407 26 C230 48 70 105 0 196 Z" fill="var(--ink)"/>
    </svg>

    <div class="back-brand">
      <div class="brand-square"></div>
      <div class="brand-name">RIDGECREST<span>BUILD</span></div>
    </div>

    <div class="person">
      <div class="person-name">MARCUS HALE</div>
      <div class="person-title">OWNER-CEO</div>
    </div>

    <ul class="contacts">
      <li><svg viewBox="0 0 16 16"><path d="M2 6 C2 3 14 3 14 6 L12 7 L11 5.5 H5 L4 7 Z M4 8 H12 L13 13 H3 Z"/></svg>123 456 789</li>
      <li><svg viewBox="0 0 16 16"><path d="M4 1 H12 V15 H4 Z M5.3 2.5 V12 H10.7 V2.5 Z" fill-rule="evenodd"/></svg>123 456 789</li>
      <li><svg viewBox="0 0 16 16"><path d="M1 4 H15 V12 H1 Z M2 5 L8 9 L14 5 Z" fill-rule="evenodd"/></svg>info@yourgmail.com</li>
      <li><svg viewBox="0 0 16 16"><circle cx="8" cy="8" r="7"/></svg>www.yourwebsite.com</li>
    </ul>

    <div class="address">Your address, City<br>State, Zip 1234</div>
  </section>
</body>
</html>
```